UK landscaping company needs website

We, Brackwell Landscapes need a website design for a company based in Surrey, UK. The design should be bold and playful. We have three main areas of work driveways, paving and fencing. It shouldn't be too heavy in text and concentrate on the pictures from previous jobs we've completed. You may use stock images for the design, these can be changed if you are successful. Please don’t just copy the flyer it is just there to provide content.
We have a logo design which we would also like editing slightly.
Here are some of my local competitors
https://www.pelmarlandscapes.example.co.uk/

https://www.twinfirgardendesign.example.com/

https://kestbyrnlandscapes.example.co.uk/

Industry/Entity Type

Landscaping

Coding

Coded - Design and coding required

Number of Pages Required

3 page

Font styles to use
Sans Serif

Requirements
Must have
• Pictures of my previous jobs.
Must be mobile friendly
Easy to navigate
Nice to have
• Try to use different colours. It would be good to have some designs that aren’t just black and green.
I’d like some curves in the design.
Should not have
• We install hard landscaping. Think more building/construction and less plants and cutting grass.

```html
<!DOCTYPE html>
<html lang="en">
<head>
<meta charset="utf-8">
<title>Brackwell Landscapes</title>
<link href="https://fonts.googleapis.com/css2?family=Montserrat:wght@400;500;600;700&display=swap" rel="stylesheet">
<style>
:root{
  --green:#6cbf43;
  --green-dark:#5aa935;
  --yellow:#f5cc00;
  --ink:#2b2b33;
  --text:#4a4a55;
  --muted:#9a9aa6;
  --soft:#f3f3f7;
  --navy:#2d3142;
  --white:#ffffff;
}
*{margin:0;padding:0;box-sizing:border-box}
html,body{width:1200px;height:4081px;overflow:hidden}
body{font-family:'Montserrat',sans-serif;color:var(--ink);background:var(--white);position:relative}
.abs{position:absolute}
.dot{position:absolute;border-radius:50%}
.btn{position:absolute;height:42px;border-radius:21px;background:var(--green);color:var(--white);font-size:11px;font-weight:700;letter-spacing:.3px;display:flex;align-items:center;justify-content:center;text-transform:uppercase}
.btn .dot{width:30px;height:30px;left:-8px;top:-8px;background:var(--yellow);opacity:.9}
.photo{position:absolute}
/* hero */
.hero{position:absolute;left:0;top:0;width:1200px;height:677px;background:linear-gradient(110deg,#e9e9ee 0%,#dcdce3 45%,#ececf1 100%);overflow:hidden}
.topline{position:absolute;top:0;left:0;height:4px;width:1200px;background:linear-gradient(90deg,var(--green) 0 52%,var(--yellow) 52% 100%)}
.brand{position:absolute;font-weight:700;color:var(--ink);font-size:24px;letter-spacing:.5px;line-height:1}
.nav a{position:absolute;top:60px;font-size:12px;font-weight:500;color:var(--ink);text-decoration:none}
.hero-kicker{left:95px;top:264px;font-size:12px;color:var(--green);font-weight:500}
.hero-title{left:92px;top:276px;font-size:56px;font-weight:500;color:var(--ink)}
.hero-copy{left:95px;top:348px;width:370px;font-size:12.5px;line-height:19px;color:var(--text)}
/* sections */
.about{position:absolute;left:0;top:677px;width:1200px;height:805px;background:var(--white);overflow:hidden}
.h2{position:absolute;font-size:33px;font-weight:500;color:var(--ink);white-space:nowrap}
.h2 .dot{width:32px;height:32px;left:-12px;top:-6px;z-index:-1}
.body-copy{font-size:12.5px;line-height:19px;color:var(--text)}
.services{position:absolute;left:0;top:1482px;width:1200px;height:986px;background:var(--soft);overflow:hidden}
.card{position:absolute;width:262px;height:261px;background:var(--white);border-bottom:4px solid var(--yellow);text-align:center}
.card.active{background:var(--green);color:var(--white)}
.card svg.icon{position:absolute;left:101px;top:84px}
.card .name{position:absolute;left:0;right:0;top:160px;font-size:18px;font-weight:500}
.card .arrow{position:absolute;left:116px;top:210px}
.testimonials{position:absolute;left:0;top:2468px;width:1200px;height:675px;background:var(--white);overflow:hidden}
.t-item{position:absolute;width:260px;text-align:center}
.avatar{width:66px;height:66px;border-radius:50%;margin:0 auto;background:linear-gradient(135deg,#c9a68c,#8a6a58);border:3px solid #fff;box-shadow:0 3px 10px rgba(0,0,0,.15)}
.t-name{font-size:16px;font-weight:600;margin-top:30px}
.t-role{font-size:9px;color:#c2c2c8;font-style:normal;margin-top:6px}
.t-text{font-size:11.5px;line-height:19px;color:var(--text);margin:22px auto 0;width:215px}
.stars{margin-top:14px;color:var(--yellow);font-size:14px;letter-spacing:3px}
.gallery{position:absolute;left:0;top:3143px;width:1200px;height:515px}
.tile{position:absolute;overflow:hidden}
.tile .label{position:absolute;left:24px;bottom:30px;color:#fff;font-size:18px;font-weight:600}
.tile .plus{position:absolute;right:20px;bottom:26px;width:20px;height:20px;border:2px solid #fff;border-radius:2px}
.tile .plus:before,.tile .plus:after{content:"";position:absolute;background:#fff;left:50%;top:50%;transform:translate(-50%,-50%)}
.tile .plus:before{width:10px;height:2px}.tile .plus:after{width:2px;height:10px}
.shade{position:absolute;left:0;right:0;bottom:0;height:45%;background:linear-gradient(180deg,rgba(0,0,0,0),rgba(0,0,0,.7))}
.footer{position:absolute;left:0;top:3658px;width:1200px;height:423px;background:var(--navy);color:#fff;overflow:hidden}
.f-col{position:absolute;top:160px}
.f-col h4{font-size:15px;font-weight:500;position:relative}
.f-col h4 .dot{width:22px;height:22px;left:-10px;top:-6px;z-index:0}
.f-col h4 span{position:relative}
.f-col a{display:block;color:#8fa0c8;font-size:13px;text-decoration:none;margin-top:14px}
.f-contact{position:absolute;left:146px;font-size:13px;display:flex;align-items:center;gap:12px}
.f-contact i{width:22px;height:22px;border-radius:50%;background:var(--green);display:inline-flex;align-items:center;justify-content:center}
.social{position:absolute;top:3934px;width:26px;height:26px;border-radius:50%}
</style>
</head>
<body>

<!-- HERO -->
<section class="hero">
  <div class="abs" role="img" aria-label="Faded photograph of a house with a garden driveway" style="left:0;top:0;width:560px;height:677px;background:linear-gradient(180deg,#d6d6dd,#e6e6ec 60%,#dadae1);opacity:.8"></div>
  <div class="topline"></div>
  <svg class="abs" style="left:0;top:0" width="1200" height="677">
    <circle cx="1245" cy="150" r="255" fill="none" stroke="var(--green)" stroke-width="9"/>
    <polygon points="563,115 1095,124 1118,607 548,600" fill="var(--yellow)"/>
    <circle cx="566" cy="566" r="61" fill="none" stroke="var(--yellow)" stroke-width="8"/>
  </svg>
  <div class="photo" role="img" aria-label="Photograph of a two-storey grey house with a paved driveway and lawn" style="left:537px;top:135px;width:557px;height:467px;background:linear-gradient(180deg,#d8e2ee 0%,#a9b0a8 35%,#8b9180 60%,#a9a9a4 80%,#7b9a4e 100%)"></div>
  <div class="abs" style="left:537px;top:500px;width:97px;height:90px;background:var(--green)"></div>
  <svg class="abs" style="left:566px;top:542px" width="40" height="16"><path d="M10 3 5 8l5 5M5 8h9M30 3l5 5-5 5M35 8h-9" stroke="#fff" stroke-width="1.8" fill="none"/></svg>

  <div class="brand" style="left:92px;top:42px;font-size:28px">Brackwell Landscapes</div>
  <nav class="nav">
    <span class="dot" style="left:553px;top:55px;width:12px;height:12px;background:var(--yellow)"></span>
    <a style="left:562px">Home</a><a style="left:634px">About</a><a style="left:709px">Services</a><a style="left:796px">Gallery</a>
  </nav>
  <span class="dot" style="left:875px;top:30px;width:32px;height:32px;background:var(--yellow)"></span>
  <span class="dot" style="left:884px;top:44px;width:30px;height:30px;background:var(--green)"></span>
  <svg class="abs" style="left:891px;top:51px" width="16" height="16" viewBox="0 0 24 24"><path d="M6.6 10.8a15 15 0 0 0 6.6 6.6l2.2-2.2c.3-.3.7-.4 1-.2 1.1.4 2.3.6 3.6.6.6 0 1 .4 1 1V20c0 .6-.4 1-1 1A17 17 0 0 1 3 4c0-.6.4-1 1-1h3.5c.6 0 1 .4 1 1 0 1.3.2 2.5.6 3.6.1.3 0 .7-.2 1z" fill="#fff"/></svg>
  <div class="abs" style="left:926px;top:49px;font-size:9px;color:var(--yellow)">Call for free estimate</div>
  <div class="abs" style="left:925px;top:62px;font-size:14px;font-weight:500">07700 900 418</div>

  <div class="abs hero-kicker">Welcome to Brackwell Landscapes</div>
  <h1 class="abs hero-title">Driveways</h1>
  <p class="abs hero-copy">We at Brackwell Landscapes are a professional, experienced landscaping business that delivers premium garden</p>
  <div class="btn" style="left:98px;top:417px;width:225px"><span class="dot"></span>Call for a free estimate</div>
</section>

<!-- ABOUT -->
<section class="about">
  <svg class="abs" style="left:0;top:0" width="1200" height="805">
    <circle cx="-60" cy="210" r="190" fill="none" stroke="var(--green)" stroke-width="9"/>
    <circle cx="288" cy="640" r="60" fill="none" stroke="var(--yellow)" stroke-width="9"/>
    <polygon points="86,112 272,108 278,320 82,322" fill="var(--green)"/>
    <polygon points="298,140 510,138 506,425 302,422" fill="var(--yellow)"/>
    <polygon points="64,345 286,337 290,630 70,636" fill="var(--yellow)"/>
    <polygon points="302,452 508,450 494,660 300,650" fill="var(--green)"/>
  </svg>
  <div class="photo" role="img" aria-label="Photograph of a timber pergola over a light stone patio" style="left:81px;top:119px;width:203px;height:195px;background:linear-gradient(180deg,#6c4e3a,#8e7a6a 45%,#c9c8c4 75%,#d6d6d4)"></div>
  <div class="photo" role="img" aria-label="Photograph of a raised timber deck and sleepers beside a lawn" style="left:301px;top:141px;width:203px;height:287px;background:linear-gradient(180deg,#c8ad7a,#b89560 30%,#3f6b2a 55%,#4d7a32 75%,#8a6a45)"></div>
  <div class="photo" role="img" aria-label="Photograph of a circular sandstone patio in front of a house" style="left:81px;top:339px;width:203px;height:289px;background:linear-gradient(180deg,#9aa0a2,#b9b0a5 40%,#c6a99a 70%,#bda295)"></div>
  <div class="photo" role="img" aria-label="Photograph of a dark block paving path with curved steps" style="left:301px;top:453px;width:203px;height:195px;background:linear-gradient(180deg,#e2e2e4,#6d6f72 40%,#4a4c50 80%,#5b5d61)"></div>

  <div class="h2" style="left:603px;top:244px;font-size:30px"><span class="dot" style="background:var(--green)"></span>About Brackwell</div>
  <div class="abs body-copy" style="left:609px;top:313px;width:440px">
    <p>We at Brackwell Landscapes are a professional, experienced landscaping business that delivers premium garden construction at an affordable price. We provide all aspects of hard and soft landscaping throughout Surrey and surrounding areas.</p>
    <p style="margin-top:18px">We pride ourselves on excellent workmanship and attention to detail. Using only top quality materials to ensure an outstanding and long-lasting finish, installed using both traditional and modern techniques.</p>
  </div>
  <div class="btn" style="left:609px;top:517px;width:222px"><span class="dot"></span>Call for a free estimate</div>
</section>

<!-- SERVICES -->
<section class="services">
  <svg class="abs" style="left:0;top:0" width="1200" height="986">
    <circle cx="1205" cy="293" r="206" fill="none" stroke="var(--green)" stroke-width="9"/>
    <circle cx="90" cy="833" r="215" fill="var(--yellow)"/>
  </svg>
  <div class="h2" style="left:440px;top:100px"><span class="dot" style="background:var(--yellow)"></span>Services we provide</div>
  <p class="abs" style="left:360px;top:155px;width:480px;text-align:center;font-size:12px;line-height:19px;color:var(--muted)">It is a long established fact that a reader will be distracted by the readable content of a page when looking at its layout.</p>

  <div class="card" style="left:187px;top:238px">
    <svg class="icon" width="60" height="56" viewBox="0 0 60 56"><rect x="22" y="2" width="16" height="16" transform="rotate(45 30 10)" fill="var(--green)"/><rect x="8" y="18" width="16" height="16" transform="rotate(45 16 26)" fill="var(--green)"/><rect x="22" y="18" width="16" height="16" transform="rotate(45 30 26)" fill="var(--ink)"/><rect x="36" y="18" width="16" height="16" transform="rotate(45 44 26)" fill="var(--ink)"/><rect x="22" y="34" width="16" height="16" transform="rotate(45 30 42)" fill="var(--ink)"/></svg>
    <div class="name">Driveways</div>
    <svg class="arrow" width="30" height="12"><path d="M2 6h25M21 1l6 5-6 5" stroke="#bbb" stroke-width="1.5" fill="none"/></svg>
  </div>
  <div class="card active" style="left:469px;top:238px">
    <svg class="icon" width="60" height="56" viewBox="0 0 60 56"><g fill="#fff"><rect x="4" y="40" width="52" height="5"/><rect x="4" y="48" width="52" height="5"/><rect x="13" y="18" width="3" height="22"/><rect x="43" y="8" width="3" height="32"/><path d="M14 26c-5-1-7-4-7-6 4 0 6 2 7 6zm1 0c5-1 7-4 7-6-4 0-6 2-7 6zM44 16c-5-1-7-4-7-6 4 0 6 2 7 6zm1 0c5-1 7-4 7-6-4 0-6 2-7 6zm-1 12c-5-1-7-4-7-6 4 0 6 2 7 6zm1 0c5-1 7-4 7-6-4 0-6 2-7 6z"/></g></svg>
    <div class="name">Garden Design</div>
    <svg class="arrow" width="30" height="12"><path d="M2 6h25M21 1l6 5-6 5" stroke="#fff" stroke-width="2" fill="none"/></svg>
  </div>
  <div class="card" style="left:750px;top:238px">
    <svg class="icon" width="60" height="56" viewBox="0 0 60 56"><rect x="22" y="2" width="16" height="16" transform="rotate(45 30 10)" fill="var(--green)"/><rect x="8" y="18" width="16" height="16" transform="rotate(45 16 26)" fill="var(--ink)"/><rect x="36" y="18" width="16" height="16" transform="rotate(45 44 26)" fill="var(--ink)"/><rect x="22" y="34" width="16" height="16" transform="rotate(45 30 42)" fill="var(--green)"/></svg>
    <div class="name">Paving &amp; Brickwork</div>
    <svg class="arrow" width="30" height="12"><path d="M2 6h25M21 1l6 5-6 5" stroke="#bbb" stroke-width="1.5" fill="none"/></svg>
  </div>
  <div class="card" style="left:187px;top:520px">
    <svg class="icon" width="60" height="60" viewBox="0 0 60 60"><path d="M29 30V18c0-6-5-10-12-10 0 7 5 11 12 10zm2-6c0-6 5-10 12-10 0 7-5 11-12 10z" fill="var(--green)"/><path d="M6 56c0-12 10-20 24-20s24 8 24 20z" fill="var(--ink)"/></svg>
    <div class="name">Planting &amp; Turfing</div>
    <svg class="arrow" width="30" height="12"><path d="M2 6h25M21 1l6 5-6 5" stroke="#bbb" stroke-width="1.5" fill="none"/></svg>
  </div>
  <div class="card" style="left:469px;top:520px">
    <svg class="icon" width="60" height="56" viewBox="0 0 60 56"><g fill="var(--ink)"><path d="M4 8l5-6 5 6v46H4zM18 8l5-6 5 6v46H18zM32 8l5-6 5 6v46H32zM46 8l5-6 5 6v46H46z"/></g><rect x="0" y="18" width="60" height="8" fill="var(--green)"/><rect x="0" y="36" width="60" height="8" fill="var(--green)"/></svg>
    <div class="name">Fencing &amp; Decking</div>
    <svg class="arrow" width="30" height="12"><path d="M2 6h25M21 1l6 5-6 5" stroke="#bbb" stroke-width="1.5" fill="none"/></svg>
  </div>
  <div class="card" style="left:750px;top:520px">
    <svg class="icon" width="60" height="56" viewBox="0 0 60 56"><path d="M4 56C4 40 8 30 14 24c-2 10-1 22 2 32zM18 56c0-20 4-36 14-48-6 14-7 32-4 48zM34 56c2-14 8-26 18-32-6 10-8 20-8 32zM48 56c2-8 6-14 10-16-2 6-2 10-2 16z" fill="var(--green)"/><path d="M12 56c2-12 6-20 10-24-2 8-2 16-1 24zM38 56c-2-12 0-24 4-30 0 10 2 20 4 30z" fill="var(--ink)"/></svg>
    <div class="name">Artificial Grass</div>
    <svg class="arrow" width="30" height="12"><path d="M2 6h25M21 1l6 5-6 5" stroke="#bbb" stroke-width="1.5" fill="none"/></svg>
  </div>

  <div class="abs" role="img" aria-label="Close-up band of green grass blades along the bottom of the section" style="left:280px;top:810px;width:920px;height:176px;background:linear-gradient(180deg,rgba(120,200,60,0) 0%,#8fd14b 25%,#5fb02e 60%,#2f7a1a 100%)"></div>
</section>

<!-- TESTIMONIALS -->
<section class="testimonials">
  <svg class="abs" style="left:0;top:0" width="1200" height="675">
    <circle cx="1210" cy="635" r="178" fill="var(--green)"/>
    <circle cx="463" cy="528" r="40" fill="none" stroke="var(--yellow)" stroke-width="8"/>
  </svg>
  <div class="h2" style="left:500px;top:128px"><span class="dot" style="background:var(--green)"></span>Testimonials</div>
  <p class="abs" style="left:350px;top:172px;width:500px;text-align:center;font-size:11px;color:var(--muted)">Lorem Ipsum is simply dummy text of the printing and typesetting</p>

  <div class="abs" style="left:457px;top:293px;width:287px;height:240px;background:#fff;box-shadow:0 6px 24px rgba(0,0,0,.08)"></div>
  <div class="t-item" style="left:181px;top:260px">
    <div class="avatar" role="img" aria-label="Portrait of client Mara Dunlow"></div>
    <div class="t-name">Mara Dunlow</div><div class="t-role">Brightfield Inc</div>
    <p class="t-text">It is a long established fact that a reader will be distracted by the readable content of a page when</p>
    <div class="stars">★★★☆☆</div>
  </div>
  <div class="t-item" style="left:470px;top:260px">
    <div class="avatar" role="img" aria-label="Portrait of client Tobias Ferne" style="background:linear-gradient(135deg,#f3b6c8,#7a4a3a)"></div>
    <div class="t-name">Tobias Ferne</div><div class="t-role">Head of Affiliate Marketing, Telvio</div>
    <p class="t-text">It is a long established fact that a reader will be distracted by the readable content of a page when</p>
    <div class="stars">★★★★★</div>
  </div>
  <div class="t-item" style="left:761px;top:260px">
    <div class="avatar" role="img" aria-label="Portrait of client Mara Dunlow" style="background:linear-gradient(135deg,#e6e6ea,#b89a80)"></div>
    <div class="t-name">Mara Dunlow</div><div class="t-role">Brightfield Inc</div>
    <p class="t-text">It is a long established fact that a reader will be distracted by the readable content of a page when</p>
    <div class="stars">★★★☆☆</div>
  </div>
</section>

<!-- GALLERY -->
<section class="gallery">
  <div class="tile" role="img" aria-label="Photograph of a new timber fence and lawn behind a brick house" style="left:0;top:0;width:544px;height:515px;background:linear-gradient(180deg,#cfd9e6,#8a6a55 25%,#9c8466 45%,#7e6a52 60%,#6fa040 80%,#4d8a2a)">
    <div class="shade"></div><div class="label">Image Name</div><div class="plus"></div></div>
  <div class="tile" role="img" aria-label="Photograph of a timber pergola over a paved patio" style="left:544px;top:0;width:328px;height:262px;background:linear-gradient(180deg,#d9dde3,#a68a68 40%,#6e6458 75%,#4b4b4b)">
    <div class="shade"></div><div class="label">Image Name</div><div class="plus"></div></div>
  <div class="tile" role="img" aria-label="Photograph of a fenced garden with lawn and raised planter" style="left:872px;top:0;width:328px;height:262px;background:linear-gradient(180deg,#a7b8cc,#a07e5a 30%,#c7bfae 60%,#6d9a3c 85%)">
    <div class="shade"></div><div class="label">Image Name</div><div class="plus"></div></div>
  <div class="tile" role="img" aria-label="Photograph of a paved patio with lawn and brick wall" style="left:544px;top:262px;width:412px;height:253px;background:linear-gradient(180deg,#7a5848,#6c9a3a 35%,#a79d8c 65%,#7a7068)">
    <div class="shade"></div><div class="label">Image Name</div><div class="plus"></div></div>
  <div class="tile" style="left:956px;top:262px;width:244px;height:253px;background:var(--green);text-align:center;color:#fff">
    <div style="position:absolute;left:0;right:0;top:56px;font-size:22px;font-weight:700">Brackwell</div>
    <p style="position:absolute;left:20px;right:20px;top:110px;font-size:11.5px;line-height:15px">Book with us directly and get the best available rate</p>
    <span class="dot" style="left:50px;top:154px;width:26px;height:26px;background:var(--yellow)"></span>
    <div style="position:absolute;left:59px;top:162px;width:125px;height:32px;border-radius:16px;background:#fff;color:var(--green);font-size:11px;font-weight:600;line-height:32px">VIEW MORE</div>
  </div>
</section>

<!-- FOOTER -->
<footer class="footer">
  <svg class="abs" style="left:0;top:0" width="1200" height="423">
    <circle cx="-20" cy="60" r="205" fill="none" stroke="var(--green)" stroke-width="8"/>
    <circle cx="1200" cy="423" r="120" fill="var(--yellow)"/>
    <line x1="146" y1="352" x2="1054" y2="352" stroke="#3d4254" stroke-width="1"/>
    <line x1="666" y1="158" x2="666" y2="238" stroke="#3d4254"/>
    <line x1="896" y1="158" x2="896" y2="238" stroke="#3d4254"/>
  </svg>
  <div class="brand" style="left:146px;top:112px;color:#fff;font-size:26px">Brackwell</div>
  <div class="f-contact" style="top:186px"><i><svg width="12" height="12" viewBox="0 0 24 24"><path d="M6.6 10.8a15 15 0 0 0 6.6 6.6l2.2-2.2c.3-.3.7-.4 1-.2 1.1.4 2.3.6 3.6.6.6 0 1 .4 1 1V20c0 .6-.4 1-1 1A17 17 0 0 1 3 4c0-.6.4-1 1-1h3.5c.6 0 1 .4 1 1 0 1.3.2 2.5.6 3.6.1.3 0 .7-.2 1z" fill="#fff"/></svg></i>07700 900 418</div>
  <div class="f-contact" style="top:219px"><i><svg width="12" height="10" viewBox="0 0 24 18"><rect x="1" y="1" width="22" height="16" rx="2" fill="#fff"/><path d="M2 2l10 8 10-8" stroke="var(--green)" stroke-width="2" fill="none"/></svg></i>info@brackwell-landscapes.example.com</div>
  <span class="social" style="left:146px;top:276px;background:#3b6fd1"></span>
  <span class="social" style="left:181px;top:276px;background:#2ea3e8"></span>
  <span class="social" style="left:216px;top:276px;background:#e23a3a"></span>

  <div class="f-col" style="left:523px"><h4><span class="dot" style="background:var(--green)"></span><span>Quick Links</span></h4><a>Home</a><a>About</a><a>Contact</a></div>
  <div class="f-col" style="left:726px"><h4><span class="dot" style="background:var(--yellow)"></span><span>Sell to Properly</span></h4><a>How it works</a><a>Pricing</a><a>Request Offer</a></div>
  <div class="f-col" style="left:953px"><h4><span class="dot" style="background:var(--green)"></span><span>Legal</span></h4><a>Terms of use</a><a>Privacy Policy</a></div>

  <div class="abs" style="left:0;right:0;top:385px;text-align:center;font-size:14px;font-weight:500">Copyright © 2020 <span style="color:var(--green)">Brackwell Landscapes</span></div>
</footer>

</body>
</html>
```